Kestrel Facilities Business Card Design

We would now like to design business cards with the new Kestrel Facilities logo

Target Market(s)

Professional

Industry/Entity Type

Professional services

Contact Information for Business Card

Employee name, title, phone number, email address, corporate office address and logo.

Font styles to use
Sans Serif

Colors
0054AA
0677BA
7BADD7
CADEEF
E8F1F8

Requirements
Must have
• My logo
Should not have
• any other pictures or images besides my logo

```html
<!DOCTYPE html>
<html lang="en">
<head>
<meta charset="utf-8">
<title>Kestrel Facilities Business Card</title>
<link href="https://fonts.googleapis.com/css2?family=Montserrat:wght@400;500;700&family=Josefin+Sans:wght@400&display=swap" rel="stylesheet">
<style>
  :root {
    --brand-blue: #3878bf;
    --ink: #1e1e1e;
    --card: #ffffff;
    --backdrop: #8f8f8f;
    --band-grey: #8a8a8a;
  }
  * { margin: 0; padding: 0; box-sizing: border-box; }
  html, body { width: 1160px; height: 1200px; overflow: hidden; }
  body { background: var(--backdrop); position: relative; font-family: "Montserrat", sans-serif; }

  .card { position: absolute; left: 199px; width: 777px; background: var(--card); overflow: hidden; }
  .card--front { top: 104px; height: 442px; }
  .card--back { top: 634px; height: 444px; }

  .brand { position: absolute; display: flex; align-items: center; color: var(--brand-blue);
    font-family: "Montserrat", sans-serif; font-weight: 700; text-transform: uppercase; }
  .brand__mark { background: var(--brand-blue); flex: none; }
  .brand__name { line-height: 1.05; letter-spacing: 1px; }

  .card--front .brand { left: 63px; top: 233px; top: 129px; height: 202px; gap: 16px; }
  .card--front .brand__mark { width: 58px; height: 58px; }
  .card--front .brand__name { font-size: 38px; }

  .card--back .brand { left: 0; right: 0; justify-content: center; top: 121px; height: 202px; gap: 20px; }
  .card--back .brand__mark { width: 70px; height: 70px; }
  .card--back .brand__name { font-size: 46px; }

  .divider { position: absolute; left: 407px; top: 113px; width: 2px; height: 231px; background: var(--brand-blue); }

  .details { position: absolute; left: 442px; top: 112px; color: var(--ink); }
  .details__name { font-weight: 700; font-size: 29px; color: var(--brand-blue); line-height: 1; letter-spacing: 0.2px; }
  .details__title { font-size: 20px; font-weight: 500; margin-top: 8px; }
  .details__address { font-family: "Josefin Sans", sans-serif; font-size: 20px; line-height: 30px; margin-top: 20px; }
  .contact { list-style: none; margin-top: 14px; }
  .contact__item { display: flex; align-items: center; gap: 7px; font-size: 20.5px; font-weight: 500; height: 29.5px; }
  .contact__icon { width: 19px; height: 19px; flex: none; }

  .band { position: absolute; left: 0; bottom: 0; width: 777px; height: 13px; }
</style>
</head>
<body>
  <section class="card card--front">
    <div class="brand">
      <span class="brand__mark"></span>
      <span class="brand__name">Kestrel<br>Facilities</span>
    </div>
    <div class="divider"></div>
    <div class="details">
      <h1 class="details__name">WANJIRU ACHIENG</h1>
      <p class="details__title">Co-Founder</p>
      <p class="details__address">P.O Box 4180-00200<br>Nairobi, Kenya</p>
      <ul class="contact">
        <li class="contact__item">
          <svg class="contact__icon" viewBox="0 0 20 20" aria-hidden="true"><path fill="#3878bf" d="M1 7c0-3 4-4 9-4s9 1 9 4v2h-5V7H6v2H1z"/><rect x="3" y="9" width="14" height="9" rx="1.5" fill="#3878bf"/><g fill="#fff"><rect x="6" y="11" width="2" height="1.5"/><rect x="9" y="11" width="2" height="1.5"/><rect x="12" y="11" width="2" height="1.5"/><rect x="6" y="14" width="2" height="1.5"/><rect x="9" y="14" width="2" height="1.5"/><rect x="12" y="14" width="2" height="1.5"/></g></svg>
          +254-163-47215
        </li>
        <li class="contact__item">
          <svg class="contact__icon" viewBox="0 0 20 20" aria-hidden="true"><rect x="1" y="4" width="18" height="12" fill="#3878bf"/><path d="M1.5 5l8.5 6 8.5-6M1.5 15.5l6-5M18.5 15.5l-6-5" stroke="#fff" stroke-width="1.4" fill="none"/></svg>
          info@kestrelfacilities.com
        </li>
        <li class="contact__item">
          <svg class="contact__icon" viewBox="0 0 20 20" aria-hidden="true"><circle cx="10" cy="10" r="9" fill="#3878bf"/><path d="M5 5c2 1 3 3 2 5s1 3 0 5M12 3c-1 2 2 3 4 4s1 4-1 5-1 3 0 4" stroke="#fff" stroke-width="1.6" fill="none"/></svg>
          www.kestrelfacilities.com
        </li>
      </ul>
    </div>
    <svg class="band" viewBox="0 0 777 13" preserveAspectRatio="none" aria-hidden="true">
      <polygon points="0,0 405,0 392,13 0,13" fill="#3878bf"/>
      <polygon points="419,0 777,0 777,13 406,13" fill="#8a8a8a"/>
    </svg>
  </section>

  <section class="card card--back">
    <div class="brand">
      <span class="brand__mark"></span>
      <span class="brand__name">Kestrel<br>Facilities</span>
    </div>
  </section>
</body>
</html>
```